Website for Ashcombe Tube Drift

Require a website for a river float in the City of Edmonton. Located on North Saskatchewan River. Will need to be a coded website with incorporated booking system through Fare Harbor software.

Pages include
Home
Pricing
About
FAQ
Contact

Ashcombe Tube Drift is an activity based business that will have customers floating down the North Saskatchewan river in Edmonton AB. The site will have all information needed and a full reservation system. The project was launched to provide people in the Edmonton area a favorite summer activity.

Here are similar websites to reference what our business will be doing and what we are looking for.

mossbankfloatco.com
quillpointpaddles.com

Target Market(s)

Families, Groups, Individuals, Anyone who wants to explore the river

Industry/Entity Type

Activities based business/ Outdoor recreational/ River Float

Coding

Coded - Design and coding required

Number of Pages Required

5+ page

Colors
0054AA
0677BA
7BADD7
CADEEF
E8F1F8
F0912C
F2A743
F7CA91
FBE8D2
FDF5EE

```html
<!DOCTYPE html>
<html lang="en">
<head>
<meta charset="utf-8">
<title>Ashcombe Tube Drift</title>
<link href="https://fonts.googleapis.com/css2?family=Fredoka:wght@600;700&family=Montserrat:ital,wght@0,400;0,500;0,600;0,700;1,400&display=swap" rel="stylesheet">
<style>
:root{
  --navy:#0b3a6c;
  --navy-deep:#082c55;
  --ink:#13335e;
  --cyan:#4ec6e8;
  --cyan-dark:#1aa5d4;
  --sky:#7badd7;
  --mist:#e8f1f8;
  --orange:#e8582a;
  --orange-soft:#f0912c;
  --white:#ffffff;
  --line:#cadeef;
  --text:#3a4a60;
}
*{box-sizing:border-box;margin:0;padding:0}
html,body{width:1200px;height:3901px;overflow:hidden;background:var(--white)}
body{font-family:"Montserrat",sans-serif;color:var(--text)}
.page{position:relative;width:1200px;height:3901px;overflow:hidden}
.abs{position:absolute}
.head{font-family:"Fredoka",sans-serif;font-weight:700;letter-spacing:1px;text-transform:uppercase}
.btn{position:absolute;display:flex;align-items:center;justify-content:center;background:var(--cyan);color:var(--navy-deep);font-family:"Fredoka",sans-serif;font-weight:700;font-size:15px;letter-spacing:.5px;border-radius:30px;border:2px solid var(--white);box-shadow:0 4px 10px rgba(8,44,85,.35);text-transform:uppercase}

/* nav */
.nav{position:absolute;left:0;top:0;width:1200px;height:70px;background:var(--white);z-index:5}
.nav a{position:absolute;top:26px;font-family:"Fredoka",sans-serif;font-weight:700;font-size:13px;color:var(--ink);text-decoration:none;letter-spacing:.5px}
.nav a.active{color:var(--orange)}
.nav .dot{position:absolute;top:29px;width:9px;height:9px;border:2px solid var(--cyan);border-radius:50%}
.logo-disc{position:absolute;left:538px;top:4px;width:124px;height:134px;border-radius:0 0 62px 62px;background:var(--white);z-index:6;display:flex;flex-direction:column;align-items:center;justify-content:center;gap:6px}
.brand-mark{width:40px;height:40px;border-radius:50%;background:var(--cyan)}
.brand-name{font-family:"Fredoka",sans-serif;font-weight:700;font-size:14px;line-height:1.05;color:var(--navy);text-align:center;text-transform:uppercase}

/* hero */
.hero-photo{position:absolute;left:0;top:0;width:1200px;height:640px;background:linear-gradient(180deg,#7d8ea6 0%,#5e7390 30%,#4d6a55 55%,#35504a 75%,#2d4a5c 100%)}
.hero-title{position:absolute;left:0;top:262px;width:1200px;text-align:center;color:var(--white);font-size:58px;text-shadow:0 3px 8px rgba(0,0,0,.3)}
.hero-sub{position:absolute;left:0;top:344px;width:1200px;text-align:center;color:var(--white);font-size:23px;font-weight:500}

/* pricing */
.section-title{position:absolute;left:0;width:1200px;text-align:center;color:var(--ink);font-size:40px}
.side-photo{position:absolute;top:792px;height:390px;border-radius:14px;background:linear-gradient(135deg,#d9d9d9,#8d8d8d)}
.price-frame{position:absolute;left:148px;top:822px;width:902px;height:451px;border:2px solid var(--orange);border-radius:18px;transform:rotate(-1.6deg)}
.price-photo{position:absolute;left:150px;top:822px;width:900px;height:450px;border-radius:14px;background:radial-gradient(circle at 35% 50%,#3aa0e0,#1466b8 60%,#0d4f9a)}
.price-box{position:absolute;left:654px;top:856px;width:359px;height:361px;background:var(--white);border-radius:10px;overflow:visible}
.price-head{height:44px;background:var(--cyan);border-radius:10px 10px 0 0;color:var(--white);font-size:23px;text-align:center;line-height:44px}
.price-amt{position:absolute;left:36px;top:62px;font-family:"Fredoka",sans-serif;font-weight:700;color:var(--navy);font-size:30px}
.price-amt small{font-size:12px;text-transform:uppercase}
.incl{position:absolute;left:14px;top:116px;width:330px;height:201px;border:2px dashed var(--navy);border-radius:8px;padding:12px 14px}
.incl p{text-align:center;font-size:15px;color:var(--ink);font-weight:500;line-height:1.35;margin-bottom:10px}
.incl li{list-style:none;font-size:11.5px;color:var(--ink);position:relative;padding-left:18px;line-height:1.35;margin-bottom:7px}
.incl li::before{content:"";position:absolute;left:0;top:2px;width:7px;height:7px;border:2px solid var(--cyan);border-radius:50%}
.group-title{position:absolute;left:0;top:1316px;width:1200px;text-align:center;font-size:38px;color:var(--ink)}
.group-title span{color:var(--orange)}
.note{position:absolute;left:0;top:1372px;width:1200px;text-align:center;font-size:12px;font-style:italic;color:#7a8594}

/* about */
.about-bg{position:absolute;left:0;top:1530px;width:1200px;height:622px;background:linear-gradient(180deg,#0f4b86 0%,#0b3a6c 45%,#082c55 100%)}
.about-frame{position:absolute;left:52px;top:1655px;width:490px;height:375px;border:2px solid var(--orange);border-radius:10px;transform:rotate(-3deg)}
.about-photo{position:absolute;left:61px;top:1662px;width:478px;height:361px;border-radius:8px;background:linear-gradient(180deg,#b7c9d6 0%,#8fa8b8 30%,#6b7d4a 55%,#8a6a38 80%,#5e5a35 100%)}
.ring{position:absolute;border-radius:50%;border:solid var(--cyan);background:transparent}
.about-title{position:absolute;left:615px;top:1610px;color:var(--white);font-size:40px}
.about-tag{position:absolute;left:613px;top:1673px;color:var(--orange-soft);font-size:16.5px;line-height:1.65}
.about-copy{position:absolute;left:615px;top:1736px;width:510px;color:var(--white);font-size:11.3px;line-height:1.9}
.about-copy p{margin-bottom:8px}

/* faq */
.faq-list{position:absolute;left:148px;top:2296px;width:902px}
.faq-item{position:relative;background:var(--white);border:1.5px solid var(--line);border-radius:5px;height:44px;margin-bottom:12px;padding:0 46px 0 50px;font-size:13px;color:var(--ink);font-weight:500;line-height:42px}
.faq-item .q{position:absolute;left:14px;top:11px;width:20px;height:20px;border-radius:50%;background:var(--cyan);color:var(--white);font-size:12px;font-weight:700;line-height:20px;text-align:center}
.faq-item .chev{position:absolute;right:18px;top:14px}
.faq-item.open{height:113px;line-height:normal;padding-top:12px}
.faq-item.open .answer{font-size:11.3px;line-height:1.85;color:#556478;margin-top:6px;width:600px;font-weight:400}
.faq-art{position:absolute;right:80px;top:12px;width:80px;height:86px;border-radius:8px;background:linear-gradient(160deg,#e8f1f8,#cadeef)}

/* contact */
.contact-bg{position:absolute;left:0;top:2860px;width:1200px;height:1041px;background:linear-gradient(180deg,#0d4a83 0%,#0a3868 50%,#082c55 100%)}
.contact-city{position:absolute;left:0;top:3080px;width:1200px;height:520px;background:linear-gradient(180deg,rgba(255,255,255,0) 0%,rgba(160,190,220,.12) 60%,rgba(255,255,255,0) 100%)}
.contact-title{position:absolute;left:0;top:3036px;width:1200px;text-align:center;color:var(--white);font-size:40px}
.contact-sub{position:absolute;left:0;top:3088px;width:1200px;text-align:center;color:var(--white);font-size:18px;font-weight:500}
.c-icon{position:absolute;width:40px;height:40px;border-radius:50%;border:2px solid var(--cyan);display:flex;align-items:center;justify-content:center;background:rgba(78,198,232,.1)}
.c-text{position:absolute;color:var(--white);font-size:14px;font-weight:500}
.social{position:absolute;width:34px;height:34px;border-radius:50%;background:var(--cyan);border:2px solid var(--white)}
.map-frame{position:absolute;left:150px;top:3220px;width:900px;height:345px;border:2px solid var(--orange);border-radius:12px;transform:rotate(-1.2deg)}
.map{position:absolute;left:148px;top:3227px;width:900px;height:336px;border-radius:12px;background:linear-gradient(160deg,#a9c9ef 0%,#cfe6cf 28%,#d8ecd2 60%,#eef2ee 100%)}
.map-badge{position:absolute;left:218px;top:3290px;width:208px;height:208px;border-radius:50%;background:var(--navy);color:var(--white);text-align:center;font-size:15px;line-height:1.4;padding-top:42px}
.map-badge .addr{font-size:13.5px;margin-top:8px}

/* footer */
.f-head{position:absolute;top:3624px;color:var(--white);font-size:18px}
.f-links{position:absolute;left:363px;top:3666px;color:var(--white);font-size:12px;line-height:22.5px;list-style:none}
.f-logo{position:absolute;left:58px;top:3672px;display:flex;flex-direction:column;align-items:center;gap:8px;width:118px}
.f-logo .brand-name{color:var(--white);font-size:15px}
.f-logo .brand-mark{width:52px;height:52px}
.sub-text{position:absolute;left:822px;top:3667px;color:var(--white);font-size:12px}
.email{position:absolute;left:822px;top:3689px;width:320px;height:40px;background:var(--white);border-radius:22px;padding-left:20px;line-height:40px;font-size:12px;color:#8893a2}
.divider{position:absolute;left:60px;top:3832px;width:1080px;height:1px;background:rgba(255,255,255,.25)}
.copy{position:absolute;left:0;top:3866px;width:1200px;text-align:center;color:var(--white);font-size:11.5px}
</style>
</head>
<body>
<div class="page">

  <!-- hero -->
  <div class="hero-photo" role="img" aria-label="Downtown city skyline above a wide river with green tree-lined banks"></div>
  <h1 class="hero-title head">Ashcombe Tube Drift</h1>
  <p class="hero-sub">Float the North Saskatchewan through downtown Edmonton</p>
  <div class="btn" style="left:524px;top:402px;width:152px;height:40px">Book Now</div>
  <svg class="abs" style="left:0;top:440px" width="1200" height="240" viewBox="0 0 1200 240">
    <path d="M0 170 C120 110 240 150 360 130 C480 110 560 20 700 40 C820 58 900 0 1020 10 C1120 18 1160 40 1200 30 L1200 240 L0 240 Z" fill="#ffffff"/>
    <path d="M0 150 C40 120 110 110 170 120 C260 135 330 120 380 95 C460 55 520 20 620 35 C720 50 780 30 880 10 C960 -6 1040 30 1100 30 C1150 30 1180 8 1200 0 L1200 60 C1170 60 1140 80 1110 110 C1070 78 1030 45 940 60 C840 78 790 105 710 100 C620 95 560 80 500 120 C440 160 380 185 300 178 C220 172 150 198 80 200 C40 200 10 185 0 175 Z" fill="#4ec6e8"/>
  </svg>

  <!-- nav -->
  <svg class="abs" style="left:0;top:60px;z-index:4" width="1200" height="20" viewBox="0 0 1200 20">
    <path d="M0 0 H1200 V6 Q1185 14 1170 6 T1140 6 T1110 6 T1080 6 T1050 6 T1020 6 T990 6 T960 6 T930 6 T900 6 T870 6 T840 6 T810 6 T780 6 T750 6 T720 6 T690 6 T660 6 T630 6 T600 6 T570 6 T540 6 T510 6 T480 6 T450 6 T420 6 T390 6 T360 6 T330 6 T300 6 T270 6 T240 6 T210 6 T180 6 T150 6 T120 6 T90 6 T60 6 T30 6 T0 6 Z" fill="#ffffff"/>
  </svg>
  <nav class="nav">
    <a class="active" style="left:58px">HOME</a>
    <span class="dot" style="left:155px"></span>
    <a style="left:218px">PRICING</a>
    <span class="dot" style="left:330px"></span>
    <a style="left:394px">ABOUT</a>
    <a style="left:760px">FAQ</a>
    <span class="dot" style="left:827px"></span>
    <a style="left:877px">CONTACT</a>
    <span class="dot" style="left:978px"></span>
    <div class="btn" style="left:1025px;top:17px;width:114px;height:34px;font-size:13px">Book Now</div>
  </nav>
  <div class="logo-disc">
    <span class="brand-mark"></span>
    <span class="brand-name">Ashcombe<br>Tube Drift</span>
  </div>

  <!-- pricing -->
  <h2 class="section-title head" style="top:748px">Our Pricing</h2>
  <div class="side-photo" style="left:-14px;width:126px" role="img" aria-label="Black and white photo of a person carrying a float tube by the water"></div>
  <div class="side-photo" style="left:1088px;width:140px" role="img" aria-label="Black and white aerial photo of people floating on tubes"></div>
  <div class="price-frame"></div>
  <div class="price-photo" role="img" aria-label="Woman relaxing on a colourful inflatable float in blue pool water"></div>
  <div class="price-box">
    <div class="price-head head">Tube and Shuttle</div>
    <div class="price-amt">30<small> / person</small></div>
    <div class="btn" style="left:186px;top:58px;width:150px;height:40px">Book Now</div>
    <div class="incl">
      <p>We keep our pricing simple and include everything you need:</p>
      <ul style="position:relative">
        <li>Premium comfort float tube with backrest and cup holder</li>
        <li>Lifejacket</li>
        <li>Paddle</li>
        <li>Round trip shuttle service</li>
        <li>Safety training</li>
        <li style="position:absolute;left:190px;top:48px">Parking</li>
        <li style="position:absolute;left:190px;top:70px">Unlimited Fun!</li>
      </ul>
    </div>
    <div class="btn" style="left:104px;top:342px;width:152px;height:40px">Book Now</div>
  </div>
  <h2 class="group-title head">Group of <span>10</span> or more?</h2>
  <p class="note">*does not include taxes or fees</p>
  <div class="btn" style="left:524px;top:1412px;width:152px;height:42px">Contact Us</div>

  <!-- about -->
  <div class="about-bg"></div>
  <svg class="abs" style="left:0;top:1518px" width="1200" height="24" viewBox="0 0 1200 24">
    <path d="M0 12 Q15 2 30 12 T60 12 T90 12 T120 12 T150 12 T180 12 T210 12 T240 12 T270 12 T300 12 T330 12 T360 12 T390 12 T420 12 T450 12 T480 12 T510 12 T540 12 T570 12 T600 12 T630 12 T660 12 T690 12 T720 12 T750 12 T780 12 T810 12 T840 12 T870 12 T900 12 T930 12 T960 12 T990 12 T1020 12 T1050 12 T1080 12 T1110 12 T1140 12 T1170 12 T1200 12 V24 H0 Z" fill="#0f4b86"/>
  </svg>
  <svg class="abs" style="left:0;top:2140px" width="1200" height="24" viewBox="0 0 1200 24">
    <path d="M0 0 H1200 V12 Q1185 22 1170 12 T1140 12 T1110 12 T1080 12 T1050 12 T1020 12 T990 12 T960 12 T930 12 T900 12 T870 12 T840 12 T810 12 T780 12 T750 12 T720 12 T690 12 T660 12 T630 12 T600 12 T570 12 T540 12 T510 12 T480 12 T450 12 T420 12 T390 12 T360 12 T330 12 T300 12 T270 12 T240 12 T210 12 T180 12 T150 12 T120 12 T90 12 T60 12 T30 12 T0 12 Z" fill="#082c55"/>
  </svg>
  <div class="about-frame"></div>
  <div class="about-photo" role="img" aria-label="River valley with autumn trees seen from a grassy hilltop"></div>
  <span class="ring" style="left:16px;top:1617px;width:28px;height:28px;border-width:6px"></span>
  <span class="ring" style="left:40px;top:1645px;width:52px;height:52px;border-width:11px"></span>
  <span class="ring" style="left:510px;top:1995px;width:44px;height:44px;border-width:10px"></span>
  <span class="ring" style="left:548px;top:2033px;width:28px;height:28px;border-width:7px"></span>
  <h2 class="about-title head">About Us</h2>
  <p class="about-tag">Float the North Saskatchewan through downtown Edmonton<br>Edmonton's Best Summer Activity</p>
  <div class="about-copy">
    <p>We provide the lifejacket, paddle, river tube and shuttle service. You just have to show up. Ashcombe Tube Drift was launched to provide people in the Edmonton area a favorite summer activity. Nothing is better on a hot summer day, than spending it on the river and seeing Edmonton from a new perspective.</p>
    <p>Our home base and meeting spot is at <b><u>Pier Nine Landing</u></b>, by the Halden Glasshouse. This is where you will check in, and board the shuttle. The shuttle will take all floaters up river to Brookmere Park Boat Launch, where your tube will be waiting. Once on the river, you can sit back, relax, explore and enjoy the view. Once you complete the float, and arrive back at Pier Nine Landing, staff will be available to assist in exiting the river where you will return your tube and gear. Safety is our top priority, but having fun is a close second. Don't miss out on Edmonton's best summer activity.</p>
  </div>
  <div class="btn" style="left:616px;top:2028px;width:152px;height:40px">Book Now</div>

  <!-- faq -->
  <h2 class="section-title head" style="top:2222px">FAQ</h2>
  <div class="faq-list">
    <div class="faq-item"><span class="q">?</span>How do I reserve my float?<svg class="chev" width="16" height="10" viewBox="0 0 16 10"><path d="M1 1l7 7 7-7" fill="none" stroke="#f0912c" stroke-width="1.6"/></svg></div>
    <div class="faq-item"><span class="q">?</span>What safety information should I know?<svg class="chev" width="16" height="10" viewBox="0 0 16 10"><path d="M1 1l7 7 7-7" fill="none" stroke="#f0912c" stroke-width="1.6"/></svg></div>
    <div class="faq-item open"><span class="q">?</span>What is included?
      <p class="answer">We provide round trip shuttle service and everything you need to have a fun and safe time on the river. All floaters will receive round trip shuttle service, a premium tube complete with backrest and cup holder, lifejacket, paddle, safety demonstration and fun.</p>
      <div class="faq-art" role="img" aria-label="Small illustration of a shuttle van beside a signpost"></div>
      <svg class="chev" width="16" height="10" viewBox="0 0 16 10"><path d="M1 9l7-7 7 7" fill="none" stroke="#f0912c" stroke-width="1.6"/></svg></div>
    <div class="faq-item"><span class="q">?</span>What should I bring?<svg class="chev" width="16" height="10" viewBox="0 0 16 10"><path d="M1 1l7 7 7-7" fill="none" stroke="#f0912c" stroke-width="1.6"/></svg></div>
    <div class="faq-item"><span class="q">?</span>Where are you located?<svg class="chev" width="16" height="10" viewBox="0 0 16 10"><path d="M1 1l7 7 7-7" fill="none" stroke="#f0912c" stroke-width="1.6"/></svg></div>
    <div class="faq-item"><span class="q">?</span>What time should I arrive?<svg class="chev" width="16" height="10" viewBox="0 0 16 10"><path d="M1 1l7 7 7-7" fill="none" stroke="#f0912c" stroke-width="1.6"/></svg></div>
  </div>
  <div class="btn" style="left:518px;top:2720px;width:164px;height:42px;background:var(--navy);color:var(--white);border-color:var(--cyan)">View All FAQs</div>

  <!-- contact -->
  <div class="contact-bg"></div>
  <svg class="abs" style="left:0;top:2770px" width="1200" height="200" viewBox="0 0 1200 200">
    <path d="M0 150 C80 120 160 110 240 128 C330 148 400 160 480 135 C560 110 620 60 700 70 C780 80 820 110 900 105 C980 100 1040 60 1100 60 C1150 60 1180 30 1200 10 L1200 200 L0 200 Z" fill="#0d4a83"/>
    <path d="M0 120 C60 95 140 85 220 100 C300 115 340 130 400 135 C480 140 540 110 600 80 C660 50 720 40 800 40 C880 40 920 70 980 60 C1060 46 1120 20 1160 5 C1180 0 1195 0 1200 0 L1200 30 C1170 30 1150 55 1110 62 C1060 40 1020 55 960 78 C900 100 860 60 800 58 C720 56 660 90 600 120 C540 150 500 175 420 168 C340 160 300 130 220 130 C140 130 80 150 0 150 Z" fill="#4ec6e8"/>
  </svg>
  <div class="contact-city" role="img" aria-label="Faint night city skyline in the background"></div>
  <h2 class="contact-title head">Contact Us</h2>
  <p class="contact-sub">We'd love to hear from you!</p>

  <div class="c-icon" style="left:218px;top:3142px"><svg width="18" height="18" viewBox="0 0 24 24"><path d="M6.6 10.8a15 15 0 006.6 6.6l2.2-2.2a1 1 0 011-.25 11 11 0 003.6.6 1 1 0 011 1V20a1 1 0 01-1 1A17 17 0 013 4a1 1 0 011-1h3.5a1 1 0 011 1 11 11 0 00.6 3.6 1 1 0 01-.25 1z" fill="none" stroke="#4ec6e8" stroke-width="1.8"/></svg></div>
  <span class="c-text" style="left:273px;top:3154px">555XXXXXXX</span>
  <div class="c-icon" style="left:432px;top:3142px"><svg width="18" height="18" viewBox="0 0 24 24"><rect x="3" y="5" width="18" height="14" rx="2" fill="none" stroke="#4ec6e8" stroke-width="1.8"/><path d="M3 7l9 6 9-6" fill="none" stroke="#4ec6e8" stroke-width="1.8"/></svg></div>
  <span class="c-text" style="left:487px;top:3154px">info@ashcombetubedrift.com</span>
  <span class="c-text" style="left:748px;top:3154px;font-size:13px">Follow Us On:</span>
  <span class="social" style="left:852px;top:3145px" aria-label="Social profile"></span>
  <span class="social" style="left:901px;top:3145px" aria-label="Social profile"></span>
  <span class="social" style="left:950px;top:3145px" aria-label="Review profile"></span>

  <div class="map-frame"></div>
  <div class="map" role="img" aria-label="Street map of the river valley showing the launch location"></div>
  <span class="ring" style="left:198px;top:3255px;width:30px;height:30px;border-width:7px;border-color:#4ec6e8"></span>
  <span class="ring" style="left:226px;top:3290px;width:48px;height:48px;border-width:9px;border-color:#4ec6e8"></span>
  <div class="map-badge">
    Come<br>Visit Us On Float Days<br>At Pier Nine Landing
    <div style="margin:10px auto 0;width:30px;height:30px;border-radius:50%;border:2px solid var(--cyan);display:flex;align-items:center;justify-content:center"><svg width="14" height="16" viewBox="0 0 24 28"><path d="M12 26s9-9 9-15a9 9 0 00-18 0c0 6 9 15 9 15z" fill="none" stroke="#4ec6e8" stroke-width="2.4"/><circle cx="12" cy="11" r="3" fill="#4ec6e8"/></svg></div>
    <div class="addr">4120 Willow Bend Rd,<br>Edmonton, AB</div>
  </div>

  <!-- footer -->
  <h3 class="f-head head" style="left:59px">Floating 7 Days a Week</h3>
  <div class="f-logo"><span class="brand-mark"></span><span class="brand-name">Ashcombe<br>Tube Drift</span></div>
  <h3 class="f-head head" style="left:363px">Navigation</h3>
  <ul class="f-links"><li>Home</li><li>Pricing</li><li>About</li><li>FAQ</li><li>Contact</li></ul>
  <h3 class="f-head head" style="left:533px">Connect</h3>
  <div class="c-icon" style="left:536px;top:3670px;width:36px;height:36px"><svg width="16" height="16" viewBox="0 0 24 24"><rect x="3" y="5" width="18" height="14" rx="2" fill="none" stroke="#4ec6e8" stroke-width="1.8"/><path d="M3 7l9 6 9-6" fill="none" stroke="#4ec6e8" stroke-width="1.8"/></svg></div>
  <span class="c-text" style="left:581px;top:3680px;font-size:12px">info@ashcombetubedrift.com</span>
  <div class="c-icon" style="left:536px;top:3722px;width:36px;height:36px"><svg width="14" height="16" viewBox="0 0 24 28"><path d="M12 26s9-9 9-15a9 9 0 00-18 0c0 6 9 15 9 15z" fill="none" stroke="#4ec6e8" stroke-width="2.4"/><circle cx="12" cy="11" r="3" fill="#4ec6e8"/></svg></div>
  <span class="c-text" style="left:581px;top:3732px;font-size:13px">Pier Nine Landing</span>
  <h3 class="f-head head" style="left:822px">Sign Up for Our Mailing List</h3>
  <p class="sub-text">Subscribe now &amp; get latest news &amp; updates</p>
  <div class="email">Email</div>
  <div class="btn" style="left:1034px;top:3689px;width:108px;height:40px;font-size:14px">Submit</div>
  <span class="social" style="left:542px;top:3815px;width:32px;height:32px"></span>
  <span class="social" style="left:584px;top:3815px;width:32px;height:32px"></span>
  <span class="social" style="left:626px;top:3815px;width:32px;height:32px"></span>
  <div class="divider" style="width:470px"></div>
  <div class="divider" style="left:670px;width:470px"></div>
  <p class="copy">© ASHCOMBE TUBE DRIFT - 2022. All Rights Reserved.</p>
</div>
</body>
</html>
```